Wordpress Design Project

Hi- We are seeking a Wordpress Theme Design that will best serve as an introduction of our company, Tesh Kalo Trading Co, to potential international clients on the web.

We are a relationship management company that help build connections between professional music equipment manufacturers and high-volume professional music equipment users, i.e concert venue managers, equipment resellers, club owners, djs,etc.

We would like to see designs to incorporate the following:

- If possible a music theme tastefully designed into the company name/logo on the wordpress home page (not a dealbreaker without)

-We are choosing the Wordpress CMS because we're looking for the site to be more centered around our blog, which will be the main medium where we connect with clients and potential clients, where these previously strangers that we meet briefly on our travelings can get to know us better by coming to the site. The relationship, and the rapport that they feel towards my team and I, will be the key driver in determining whether they will want to do business through us or not. The products are secondary in importance. It is after the visitor feel comfortable doing business through us that they will venture to check out the products that we offer. Finally, the website is not a sales point, there will not be a feature for someone to buy something from the site.

Long story short, this website is meant to be a communications channel and not a sales channel.

-Need a contacts form application built-in to capture interested client information to facilitate the off-site sales process.

- Would prefer the theme to give a minimalist and conservative feel, and ideally capture the concept of our globalized world and the synergizing role that music plays in bringing people together.

-Ideally the design should incorporate subtle references to the Generation Y values that inspired our company name and mission:

-Emphasis on partnership and teamwork
-Belief and aspiration for win/win trade relations
-Fast, honest, and transparent service
-Make the world a better place via trade

Theme example (function-wise): http://demo2.plorvexthemes.com/?name=brit

Product Type examplex: http://www.kavro.com.cn/en/product.asp

(Willing to pay extra if the winning design can be coded to full functionality)
Updates

To all those designers who've accepted the contest invitation, can you please send me a quick message to confirm if you are still planning on submitting by the end of the day tomorrow, 8/9. Otherwise we will make a selection ahead of the deadline so we can speed up our website live date. Thanks!

Target Market(s)

High volume/frequency professional music equipment users/resellers. Concert venues, DJs, Dance Clubs, etc

Industry/Entity Type

Communications

Requirements
Must have
• Blog
Product Showcase Page that is easy to update and expand.
About Page
Contact Forms Application built-in
Nice to have
• Music theme designed into company name/logo

```html
<!DOCTYPE html>
<html lang="en">
<head>
<meta charset="utf-8">
<title>Tesh Kalo Trading Co</title>
<link href="https://fonts.googleapis.com/css2?family=PT+Sans:ital,wght@0,400;0,700;1,400&family=Ropa+Sans&display=swap" rel="stylesheet">
<style>
:root{
  --bg:#dcdee7;
  --page:#ffffff;
  --navy:#2b3a8c;
  --navy-dark:#1f2b6e;
  --ink:#2a2f4a;
  --text:#4a5070;
  --muted:#6a7090;
  --line:#cfd3e2;
  --band:#eef0f6;
  --panel:#f4f5f9;
  --field:#ffffff;
}
*{box-sizing:border-box;margin:0;padding:0}
html,body{width:824px;height:1200px;overflow:hidden}
body{background:var(--bg);font-family:"PT Sans",sans-serif;color:var(--text);position:relative}
.page{position:absolute;left:46px;top:0;width:732px;height:1135px;background:var(--page);border-top:3px solid var(--navy);box-shadow:0 0 6px rgba(0,0,0,.12)}
.header{position:absolute;left:0;top:0;width:100%;height:82px;background:linear-gradient(#fff,#f3f4f8)}
.logo{position:absolute;left:22px;top:26px;display:flex;align-items:center;gap:8px}
.logo-mark{width:26px;height:26px;background:var(--navy);border-radius:3px}
.logo-name{font-family:"Ropa Sans",sans-serif;font-size:22px;color:var(--navy)}
.nav{position:absolute;right:20px;top:42px;display:flex;gap:4px;font-family:"Ropa Sans",sans-serif;font-size:12.5px}
.nav a{color:var(--navy);text-decoration:none;padding:3px 13px;border-radius:3px}
.nav a.active{background:var(--navy);color:#fff}
.hero{position:absolute;left:0;top:82px;width:100%;height:240px;background:linear-gradient(100deg,#2c3fa0 0%,#5560a8 35%,#9aa0b8 60%,#3c4a9e 100%)}
.hero-dots{position:absolute;left:50%;bottom:0;transform:translateX(-50%);width:70px;height:16px;background:#fff;border-radius:16px 16px 0 0;display:flex;justify-content:center;align-items:center;gap:4px}
.hero-dots span{width:5px;height:5px;border-radius:50%;background:#b8bdd2}
.hero-dots span.on{background:var(--navy)}
.section-title{position:absolute;font-family:"Ropa Sans",sans-serif;font-size:15px;color:var(--navy)}
.section-title b{font-weight:400;color:var(--ink)}
.welcome-text{position:absolute;left:18px;top:370px;width:690px;font-size:8.3px;line-height:13px;color:var(--navy-dark)}
.welcome-text p+p{margin-top:13px}
.products{position:absolute;left:14px;top:488px;width:703px;height:135px;border:1px solid var(--line);display:flex}
.product{flex:1;border-right:1px solid var(--line);position:relative}
.product:last-child{border-right:0}
.product-img{position:absolute;left:20px;top:38px;width:136px;height:40px;background:linear-gradient(#3a3d48,#7a7e8c)}
.product-label{position:absolute;left:0;bottom:0;width:100%;height:30px;background:var(--band);font-size:10.5px;color:var(--navy-dark);padding:9px 10px}
.arrow{position:absolute;top:533px;width:18px;height:18px;border-radius:50%;background:#eceef3;border:1px solid #bfc3d1}
.blog-item{position:absolute;left:22px;width:520px;height:120px}
.blog-img{position:absolute;left:0;top:0;width:145px;height:117px;border:1px solid #ccc}
.blog-body{position:absolute;left:156px;top:0;width:310px}
.blog-title{font-family:"Ropa Sans",sans-serif;font-size:12.5px;color:var(--ink);margin-top:4px}
.blog-excerpt{font-size:7.8px;line-height:14px;color:var(--text);margin-top:4px}
.read-more{font-size:8.5px;color:var(--ink);margin-top:3px;letter-spacing:.2px}
.meta{display:inline-block;margin-top:6px;background:var(--panel);padding:4px 12px 4px 8px;font-size:7.5px;color:var(--navy)}
.meta big{font-size:10.5px}
.sidebar{position:absolute;left:508px;top:649px;width:214px;height:477px;background:var(--panel)}
.side-head{font-family:"Ropa Sans",sans-serif;font-size:14.5px;color:var(--navy);padding:12px 13px 7px;border-bottom:3px solid var(--navy)}
.form{padding:10px 13px 0}
.field{background:var(--field);border:1px solid #c6cad8;height:21px;font-size:8.5px;color:var(--navy);padding:5px 7px;margin-bottom:12px}
.field.message{height:92px}
.buttons{display:flex;gap:6px;margin-top:-3px}
.btn{font-size:10px;padding:4px 8px;border-radius:3px}
.btn.primary{background:var(--navy);color:#fff}
.btn.secondary{background:#e4e7f0;color:var(--navy);border:1px solid #c0c5d6}
.divider{margin-top:21px;border-top:1px solid var(--line)}
.testimonial{padding:10px 13px;font-size:8px;line-height:14px;color:var(--navy-dark);font-style:italic}
.avatar{float:left;width:59px;height:52px;margin:0 6px 2px 0;background:linear-gradient(#8a7a60,#4a4030)}
.testimonial strong{font-style:normal;font-size:10px;font-weight:400}
.testimonial .by{font-style:normal;font-family:"PT Sans",serif;font-weight:700;font-size:9px;margin-top:6px;color:var(--navy-dark)}
.footer{position:absolute;left:49px;top:1153px;font-size:8px;color:var(--navy-dark)}
</style>
</head>
<body>
<div class="page">
  <header class="header">
    <div class="logo"><span class="logo-mark"></span><span class="logo-name">Tesh Kalo Trading Co</span></div>
    <nav class="nav">
      <a class="active">Home</a><a>About Us</a><a>Blog</a><a>Products</a><a>Testimonials</a><a>Services</a><a>Contact</a>
    </nav>
  </header>

  <div class="hero" role="img" aria-label="Recording studio with mixing console, monitor speakers and audio editing screen">
    <div class="hero-dots"><span class="on"></span><span></span><span></span><span></span><span></span></div>
  </div>

  <h1 class="section-title" style="left:18px;top:342px">Welcome to <b>Tesh Kalo <span style="color:var(--navy)">Trading</span> Co</b></h1>
  <div class="welcome-text">
    <p>Brenvale eSolutions is a web service company, offering a wide range of services which range from designing and development, that is covering almost all the fields in the best possible way. To be the best we know what and how to present beautifully the working of the client's need and their advantages be highlighted. We act in accordance with the Industry certified processes to deliver the best to our clients all over the world.</p>
    <p>Thus, Wanna get ahead in the competition with other website. Brenvale esolutions provide you with an attractive and most convincing website to enhance your marketing goals. The only way to success is through the right path and that's what we provide you. None of the other companies has the result we do.</p>
  </div>

  <h2 class="section-title" style="left:16px;top:463px">Featured <b>Products</b></h2>
  <div class="products">
    <div class="product"><div class="product-img" role="img" aria-label="Rack-mount power amplifier"></div><div class="product-label">Model XM-300 &nbsp;|&nbsp; LEARN MORE</div></div>
    <div class="product"><div class="product-img" role="img" aria-label="Rack-mount power amplifier"></div><div class="product-label">Model XM-300 &nbsp;|&nbsp; LEARN MORE</div></div>
    <div class="product"><div class="product-img" role="img" aria-label="Rack-mount power amplifier"></div><div class="product-label">Model XM-300 &nbsp;|&nbsp; LEARN MORE</div></div>
    <div class="product"><div class="product-img" role="img" aria-label="Rack-mount power amplifier"></div><div class="product-label">Model XM-300 &nbsp;|&nbsp; LEARN MORE</div></div>
  </div>
  <svg class="arrow" style="left:6px" viewBox="0 0 18 18"><path d="M10.5 5 6.5 9l4 4" fill="none" stroke="#555" stroke-width="1.5"/></svg>
  <svg class="arrow" style="left:704px" viewBox="0 0 18 18"><path d="M7.5 5l4 4-4 4" fill="none" stroke="#555" stroke-width="1.5"/></svg>

  <h2 class="section-title" style="left:28px;top:633px">Recent <b>Blog</b></h2>

  <article class="blog-item" style="top:674px">
    <div class="blog-img" role="img" aria-label="Studio mixing desk with monitors and speakers" style="background:linear-gradient(135deg,#6a3a20,#2a2420 60%,#8a6a50)"></div>
    <div class="blog-body">
      <h3 class="blog-title">Vel ut quas utroque placerat, kasd utinam epicuri at</h3>
      <p class="blog-excerpt">est, hendrerit argumentum dissentias ei nec. Vel ut quas utroque placerat, kasd utinam epicuri at est, hendrerit argumentum dissentias ei nec. Vel ut quas utroque placerat, kasd utinam epicuri at est, hendrerit argumentum dissentias ei nec. Vel ut quas utroque placerat, kasd utinam epicuri at est,</p>
      <p class="read-more">CONTINUE READING &rsaquo;</p>
      <p class="meta">Posted on <big>04/02/2012</big> &nbsp; <big>| 252 Comments</big></p>
    </div>
  </article>

  <article class="blog-item" style="top:821px">
    <div class="blog-img" role="img" aria-label="Home studio desk with laptop and monitor speakers" style="background:linear-gradient(#d8d8d8,#6a6a6a 60%,#3a3a3a)"></div>
    <div class="blog-body">
      <h3 class="blog-title">kasd utinam epicuri</h3>
      <p class="blog-excerpt">est, hendrerit argumentum dissentias ei nec. Vel ut quas utroque placerat, kasd utinam epicuri at est, hendrerit argumentum dissentias ei nec. Vel ut quas utroque placerat, kasd utinam epicuri at est, hendrerit argumentum dissentias ei nec. Vel ut quas utroque placerat, kasd utinam epicuri at est,</p>
      <p class="read-more">CONTINUE READING &rsaquo;</p>
      <p class="meta">Posted on <big>04/02/2012</big> &nbsp; <big>| 252 Comments</big></p>
    </div>
  </article>

  <article class="blog-item" style="top:969px">
    <div class="blog-img" role="img" aria-label="Engineer beside a rack of studio equipment" style="background:linear-gradient(90deg,#6a5a50,#2a2c30 55%,#3a3c44)"></div>
    <div class="blog-body">
      <h3 class="blog-title">Pellentesque habitant morbi tristique senectus</h3>
      <p class="blog-excerpt">est, hendrerit argumentum dissentias ei nec. Vel ut quas utroque placerat, kasd utinam epicuri at est, hendrerit argumentum dissentias ei nec. Vel ut quas utroque placerat, kasd utinam epicuri at est, hendrerit argumentum dissentias ei nec. Vel ut quas utroque placerat, kasd utinam epicuri at est,</p>
      <p class="read-more">CONTINUE READING &rsaquo;</p>
      <p class="meta">Posted on <big>04/02/2012</big> &nbsp; <big>| 252 Comments</big></p>
    </div>
  </article>

  <aside class="sidebar">
    <h2 class="side-head">Quick Contact Form</h2>
    <div class="form">
      <div class="field">type your name</div>
      <div class="field">type your email address</div>
      <div class="field">type your phone no.</div>
      <div class="field message">query/message</div>
      <div class="buttons"><span class="btn primary">Submit Now</span><span class="btn secondary">Reset Now</span></div>
    </div>
    <div class="divider"></div>
    <h2 class="side-head">Testimonials</h2>
    <div class="testimonial">
      <div class="avatar" role="img" aria-label="Client portrait"></div>
      <strong>Tittle line goes here</strong> advanced web projects and the ongoing projects that require permanent maintenance and support We like challenges and do complete these challenge with expertise We at Brenvale provide you the best simple websites too with total work done as using
      <p class="by">By Author Name</p>
    </div>
  </aside>
</div>

<footer class="footer">&copy; 2012 Company Name &nbsp;|&nbsp; All right reserved &nbsp;|&nbsp; Term &amp; Conditions</footer>
</body>
</html>
```